Push notification screens at app start up

We have an existing news publication app platform and are adding categories to push notifications.

We need two screens designed (each for Zorbel, Quillet and Android for a total of 6d) that show when the app is first launched.

The workflow of our app:
0. app launch screen while webservices run (no work needed)
1. information screen to the user promoting the benefits of push notification with "Next" button. (see concept attached)
2. Push categories selection screen. This will have list of category types, with on/off switch.

"Select the categories that you wish to receive occasional notices:
Breaking News (on/off switch)
Local News (on/off switch)
Sports (on/off switch)
Local Events (on/off switch)
Weather Alerts (on/off switch)
Local Deals (on/off switch)"

"Enable these categories on the next screen."
"Next" button

Background:
When I was looking around at app designs, I came across this one (http://www.plinthworks.example/design/7719034) and I really liked it. We obviously have different features on our screen, but I’d like to have this same feel. The colors used in this design are perfect.

UPDATE: I do not mean to limit your design to match the layout as the one mentioned above. Please use your creativity for the layout.

Our standard font in Helvetica Neue.

Notes:
- our app is developed for all phone devices from Zorbel 4 to Zorbel 6, so designs should be thoughtful of vertical scrolling if needed.
- our app is developed for Quillets, so we'll need designs completed as well. (We can finalize Zorbel design first, then translate the design to Quillet.)
- our app is developed for Android phones (not tablets), so we'll need designs completed as well. (We can finalize iOS design first, then translater to Android UI design guidelines).

We hope to establish a good on-going relationship with the designer for as-needed work in the future.

News

• Helvetica Neue

• Clean designs. No clutter.
• We would likely go with the standard on/off switches for both iOS and Android, but are open to small custom variations.

```html
<!DOCTYPE html>
<html lang="en">
<head>
<meta charset="utf-8">
<title>Notifications – Onboarding</title>
<link href="https://fonts.googleapis.com/css2?family=Roboto:wght@300;400&display=swap" rel="stylesheet">
<style>
  :root {
    --bar-black: #0b0b0b;
    --body-grey: #ebebeb;
    --text-grey: #5a5a5a;
    --title-grey: #2e2e2e;
    --accent-blue: #3b8fd9;
    --status-white: #f4f4f4;
  }
  * { margin: 0; padding: 0; box-sizing: border-box; }
  html, body {
    width: 1200px;
    height: 2352px;
    overflow: hidden;
    background: var(--body-grey);
    font-family: "Roboto", "Helvetica Neue", Arial, sans-serif;
  }
  .screen {
    position: relative;
    width: 1200px;
    height: 2352px;
    background: var(--body-grey);
  }
  .status-bar {
    position: absolute;
    top: 0; left: 0;
    width: 100%;
    height: 78px;
    background: var(--bar-black);
    color: var(--status-white);
    font-size: 32px;
    font-weight: 400;
    display: flex;
    align-items: center;
    justify-content: space-between;
    padding: 0 26px;
  }
  .status-left, .status-right { display: flex; align-items: center; gap: 12px; }
  .signal-dots { letter-spacing: 2px; font-size: 26px; }
  .status-time {
    position: absolute;
    left: 50%;
    transform: translateX(-50%);
  }
  .header-tab {
    position: absolute;
    top: 0; left: 0;
    width: 1200px;
    height: 500px;
  }
  .content {
    position: absolute;
    top: 650px;
    left: 50px;
    right: 50px;
    text-align: center;
    color: var(--text-grey);
  }
  .content-title {
    font-size: 50px;
    font-weight: 400;
    color: var(--title-grey);
    letter-spacing: 1px;
    margin-bottom: 40px;
  }
  .content-text {
    font-size: 45px;
    font-weight: 300;
    line-height: 66px;
    white-space: nowrap;
  }
  .content-text + .content-text { margin-top: 66px; }
  .footer-bar {
    position: absolute;
    bottom: 0; left: 0;
    width: 100%;
    height: 168px;
    background: var(--bar-black);
    display: flex;
    align-items: center;
    justify-content: center;
  }
  .next-button {
    color: var(--accent-blue);
    font-size: 44px;
    font-weight: 300;
    letter-spacing: 2px;
    text-decoration: none;
  }
</style>
</head>
<body>
<main class="screen">
  <header class="status-bar">
    <div class="status-left">
      <span class="signal-dots">●●●○○</span>
      <span class="carrier">VOLTA</span>
      <svg class="wifi-icon" width="38" height="30" viewBox="0 0 38 30" aria-hidden="true">
        <path d="M3 11 A22 22 0 0 1 35 11" fill="none" stroke="#f4f4f4" stroke-width="4"/>
        <path d="M9 17 A14 14 0 0 1 29 17" fill="none" stroke="#f4f4f4" stroke-width="4"/>
        <circle cx="19" cy="25" r="4" fill="#f4f4f4"/>
      </svg>
    </div>
    <span class="status-time">4:21 PM</span>
    <div class="status-right">
      <svg class="bluetooth-icon" width="20" height="34" viewBox="0 0 20 34" aria-hidden="true">
        <path d="M3 9 L16 24 L10 30 L10 4 L16 10 L3 25" fill="none" stroke="#f4f4f4" stroke-width="2.5"/>
      </svg>
      <span class="battery-level">100%</span>
      <svg class="battery-icon" width="58" height="28" viewBox="0 0 58 28" aria-hidden="true">
        <rect x="1.5" y="1.5" width="50" height="25" rx="3" fill="none" stroke="#f4f4f4" stroke-width="3"/>
        <rect x="6" y="6" width="41" height="16" fill="#f4f4f4"/>
        <rect x="53" y="9" width="4" height="10" fill="#f4f4f4"/>
      </svg>
    </div>
  </header>

  <svg class="header-tab" viewBox="0 0 1200 500" aria-hidden="true">
    <rect x="0" y="70" width="1200" height="95" fill="#0b0b0b"/>
    <path d="M480 160 L480 365 A120 120 0 0 0 720 365 L720 160 Z" fill="#0b0b0b"/>
    <g class="mute-icon" fill="none" stroke="#3b8fd9" stroke-width="7" stroke-linejoin="round" stroke-linecap="round">
      <path d="M550 235 L573 235 L608 202 L608 322 L573 289 L550 289 Z"/>
      <path d="M628 232 A40 40 0 0 1 628 292"/>
      <line x1="546" y1="200" x2="654" y2="325"/>
    </g>
  </svg>

  <section class="content">
    <h1 class="content-title">NOTIFICATIONS</h1>
    <p class="content-text">By enabling push notifications, you can keep<br>you up to date with occasional notifications<br>related to items you care about. Select the<br>categories on the next screen and then<br>authorize the push notifications.</p>
    <p class="content-text">If you ever change your mind, you can adjust<br>these options in the Settings menu of this app.</p>
  </section>

  <footer class="footer-bar">
    <a class="next-button" href="#">NEXT &gt;</a>
  </footer>
</main>
</body>
</html>
```